Striking new Advert required for Commercial Real Estate Agency

We need a a NEW newspaper advertisement for the marketing of a large commercial property (a Backpackers lodge)

Dimensions are to be width of 101mm and height of 100mm (10cms)

Our key design statement for this advert is clean, modern and minimalist design, with accents of 'HOT PINK' colour to remove it from looking too boring, perhaps in the area of the contact icons. The heirachy of the advert is outlined in the attached ADVERTISEMENT TEXT FILE.

Our company name is THE HARBOURLINE COLLECTIVE, and we want our brand to appear professional yet classy in it's design style (sort of like an advertising or design agency)

We have two logo options below, one more square in its layout (which we prefer) and the other more rectangular, which may be better suited for the layout. We are not adverse to the logo being reversed (white text on black), along with other key element areas such as the main advert heading and the "FOR SALE" part, and think this would be a good option.
There are two photos attached to be included in the advert.

We have attached an example of an old advert that we did, which we DID NOT LIKE, and which was for a smaller width than the one we need (it is only 65% of the width of this one). WE have also atached a file showing layout of some of our competitors adverts, which we dont think are too good either.

We are really open for ideas, but have time pressures, so please come back with any questions as soon as you can, if needed.

Thank you
Updates

Thank you for the great and diverse designs. There are a few standout options, but one style that we prefer most.

Target Market(s)

We are wanting this newspaper advertisement to attract interest from real estat e developers, investors and motel/lodge owners, along with other high nett worth individuals

Industry/Entity Type

Real Estate

Font styles to use
Serif
Sans Serif

Colors
1b1b1b
a54499
474747
fbfbfb

Requirements
Must have
• Clean modern look, predominantly monochromatic or black and white, with the hot pink accent somewhere, as mentioned above.
• All the contents of the TEXT provided, perhaps with additional space to add a little more if needed, Please advise if you think we dont have enough space for all of the TEXT
Should not have
• Script like fonts
• Cartoonish characters
• a 'cheap' look

```html
<!DOCTYPE html>
<html lang="en">
<head>
<meta charset="utf-8">
<title>For Sale – Mount Victoria Land Grab</title>
<link rel="stylesheet" href="https://fonts.googleapis.com/css2?family=Lato:wght@400;700&family=Montserrat:wght@800&display=swap">
<style>
  :root {
    --ink: #1b1b1b;
    --pink: #a54499;
    --body: #474747;
    --paper: #fbfbfb;
    --white: #ffffff;
    --backdrop: #d0d0d0;
  }
  * { margin: 0; padding: 0; box-sizing: border-box; }
  html, body { width: 1200px; height: 903px; overflow: hidden; background: var(--backdrop); }
  .advert {
    position: absolute;
    left: 286px; top: 142px;
    width: 786px; height: 778px;
    background: var(--white);
    transform: scale(0.8);
    transform-origin: top left;
    font-family: "Lato", sans-serif;
    color: var(--body);
  }
  .advert > * { position: absolute; }
  .headline {
    left: 45px; top: 20px;
    font-family: "Montserrat", sans-serif;
    font-weight: 800; font-size: 60px; line-height: 70px;
    color: var(--ink); letter-spacing: 1px;
  }
  .tagline {
    right: 42px; top: 52px;
    font-size: 22px; line-height: 28px; color: var(--ink);
  }
  .property-photo {
    left: 37px; top: 86px; width: 711px; height: 234px;
    background: linear-gradient(180deg, #4f8fd6 0%, #9cc3ea 35%, #e9ecef 55%, #c9ccd3 68%, #4d6b2e 82%, #2f4a1c 100%);
  }
  .address-band {
    left: 37px; top: 322px; width: 711px; height: 50px;
    background: var(--ink); color: var(--white);
    font-size: 25px; font-weight: 400; line-height: 50px; text-align: center;
  }
  .intro { left: 38px; top: 375px; font-size: 20px; line-height: 28px; color: var(--ink); }
  .lead { left: 38px; top: 410px; width: 706px; font-size: 20px; line-height: 26.5px; color: var(--pink); }
  .key-points { left: 38px; top: 462px; width: 706px; list-style: none; font-size: 20px; line-height: 26.5px; color: var(--ink); }
  .key-points li { position: relative; padding-left: 30px; text-align: justify; margin-bottom: 6px; }
  .key-points li::before {
    content: ""; position: absolute; left: 6px; top: 11px;
    width: 8px; height: 8px; border-radius: 50%; background: var(--pink);
  }
  sup { font-size: 11px; line-height: 0; }
  .tender {
    left: 0; top: 643px; width: 786px; text-align: center;
    font-size: 20px; font-weight: 700; color: var(--pink); line-height: 26px;
  }
  .contact-bar {
    left: 0; top: 671px; width: 786px; height: 107px;
    background: var(--ink); color: var(--white);
  }
  .contact-bar > * { position: absolute; }
  .agent-name { left: 40px; top: 4px; font-size: 22px; font-weight: 700; line-height: 28px; }
  .contact-line { display: flex; align-items: center; gap: 12px; font-size: 20px; line-height: 28px; }
  .contact-line svg { width: 16px; height: 16px; flex: none; }
  .phone-office { left: 40px; top: 34px; }
  .phone-mobile { left: 40px; top: 62px; }
  .email { left: 234px; top: 31px; }
  .website { left: 234px; top: 59px; }
  .brand-name {
    right: 26px; top: 40px;
    font-size: 15px; font-weight: 700; line-height: 26px;
    letter-spacing: 1px; color: var(--white); white-space: nowrap;
  }
</style>
</head>
<body>
  <article class="advert">
    <h1 class="headline">FOR SALE</h1>
    <p class="tagline">Mount Victoria Land Grab</p>
    <div class="property-photo" role="img" aria-label="Photo of a two-storey white weatherboard lodge with fire escapes, under blue sky with green hillside and shrubs"></div>
    <h2 class="address-band">Marigold Lodge, 42 Kestrel Street, Mount Victoria</h2>
    <p class="intro">This Old Beauty has served many, and is now ripe for development.</p>
    <p class="lead">One of Mt Vic’s largest land areas, now offered with vacant possession, with key details being:</p>
    <ul class="key-points">
      <li>Large Land area of 2076m<sup>2</sup> with elevated sunny position and great outlook + access from Alder Street</li>
      <li>Existing Backpackers Lodge of 970m<sup>2</sup> providing multiple rooms with amenity areas</li>
      <li>Four adjacent sites also available, taking total land area to 4452m<sup>2</sup>, an unprecedented Land Offering in this popular cuity fringe location</li>
    </ul>
    <p class="tender">NOW SELLING BY CLOSED TENDER</p>
    <footer class="contact-bar">
      <p class="agent-name">Dana Whitfield</p>
      <p class="contact-line phone-office">
        <svg viewBox="0 0 16 16" aria-hidden="true"><path d="M4 1.5l2.2 3-1.3 1.6c.8 1.8 2.2 3.3 4 4.1l1.6-1.3 3 2.2-1.2 2.6C7 13.5 2.5 9 1.4 3z" fill="none" stroke="#a54499" stroke-width="1.6" stroke-linejoin="round"/></svg>
        (04) 555 0142
      </p>
      <p class="contact-line phone-mobile">
        <svg viewBox="0 0 16 16" aria-hidden="true"><rect x="4" y="1" width="8" height="14" rx="1.5" fill="none" stroke="#a54499" stroke-width="1.6"/><circle cx="8" cy="12.3" r="1" fill="#a54499"/></svg>
        (021) 555 018
      </p>
      <p class="contact-line email">
        <svg viewBox="0 0 16 16" aria-hidden="true"><rect x="2" y="4" width="12" height="8" fill="#a54499"/><path d="M2 4l6 4.5L14 4" fill="none" stroke="#1b1b1b" stroke-width="1.2"/></svg>
        dana@harbourline.co.nz
      </p>
      <p class="contact-line website">
        <svg viewBox="0 0 16 16" aria-hidden="true"><g fill="none" stroke="#a54499" stroke-width="1.3"><circle cx="8" cy="8" r="6"/><ellipse cx="8" cy="8" rx="2.6" ry="6"/><path d="M2 8h12M3 5h10M3 11h10"/></g></svg>
        www.harbourline.co.nz
      </p>
      <p class="brand-name">THE HARBOURLINE COLLECTIVE</p>
    </footer>
  </article>
</body>
</html>
```